Website re-design and completion for www.brovimark.com

Graphically redesign and complete the existing site www.brovimark.com
This site intent is to:
a) introduce and educate about a new Technoloy to customers in a variety of different industries using traditional methods.
b) outline and promote the benefits and ROI of using the new techology
c) Sell our machines by showing customers the benefits and reasons to purchase from us over other suppliers
We do want to keep the overall concept. Like the home page with a slider. The most important thing to us is to increase the design of the slider. Next we need it standard layout with some attractive design to describe each product group. There are 3 product groups. Laser Cleaning Machines, Laser Welding Machines and Laser Cutting Machines

Target Market(s)

Mostly business to business.

Coding

Coded - Design and coding required

Font styles to use
Sans Serif
Other font styles liked:
• Calibri, Arial

Requirements
Must have
• A serious approach as we are targeting professionals, such as production managers, engineers and so forth
Should not have
• Annoying call to action stuff. Overly playful gimmicks.

```html
<!DOCTYPE html>
<html lang="en">
<head>
<meta charset="utf-8">
<title>Brovimark – Landing Page Mobile view</title>
<link href="https://fonts.googleapis.com/css2?family=Inter:wght@400;500;600;700&display=swap" rel="stylesheet">
<style>
:root{
  --bg:#ffffff;
  --screen:#f6f7fd;
  --card:#ffffff;
  --ink:#1d2233;
  --muted:#8a8fa3;
  --brand:#0d4f86;
  --accent:#1a86e0;
  --green:#3cc46a;
  --dark:#151617;
  --line:#e6e8f2;
  --blush:#fbeeee;
}
*{box-sizing:border-box;margin:0;padding:0}
html,body{width:1200px;height:1200px;overflow:hidden;background:var(--bg);font-family:"Inter",sans-serif;color:var(--ink)}
.page{position:relative;width:1200px;height:1200px;padding:60px 51px}
.intro{display:flex;align-items:flex-start;gap:60px;margin-bottom:34px}
.brand{display:flex;align-items:center;gap:12px}
.brand-mark{width:30px;height:30px;border-radius:50%;background:var(--brand)}
.brand-name{font-size:38px;font-weight:700;color:var(--brand);letter-spacing:2px}
.brand-tag{font-size:11px;color:var(--accent);letter-spacing:.6px;margin-top:4px;margin-left:42px}
.intro-title{font-size:30px;font-weight:500;color:var(--brand);line-height:1.2;margin-top:4px}

.board{display:grid;grid-template-columns:repeat(4,255px);gap:26px;align-items:start}
.col{display:flex;flex-direction:column;gap:22px}
.screen{background:var(--screen);border-radius:16px;padding:22px 20px;box-shadow:0 10px 30px rgba(30,40,90,.07);overflow:hidden}
.h2{font-size:17px;font-weight:600;line-height:1.25;margin-bottom:10px}
.h2.blue{color:var(--accent);font-size:20px}
.p{font-size:10.5px;color:var(--muted);line-height:1.6}
.checks{list-style:none;margin:14px 0;display:flex;flex-direction:column;gap:8px}
.checks li{display:flex;gap:8px;font-size:12px;align-items:flex-start}
.checks svg{flex:none;margin-top:2px}
.btn-outline{display:inline-flex;align-items:center;gap:10px;border:1.5px solid var(--accent);color:var(--accent);font-size:10.5px;padding:8px 14px;border-radius:4px;margin-top:6px}
.btn-solid{display:inline-flex;align-items:center;gap:10px;background:var(--accent);color:#fff;font-size:10.5px;padding:9px 16px;border-radius:3px}

.hero{background:var(--dark);color:#f3f3f3;padding:18px 20px 0}
.hero .top{display:flex;justify-content:space-between;align-items:center;margin-bottom:26px}
.hero .mini{font-size:13px;font-weight:700;color:var(--accent);letter-spacing:1px}
.hero h1{font-size:22px;font-weight:500;line-height:1.25;margin-bottom:14px}
.hero .p{color:#cfd1d6;font-size:11px;margin-bottom:18px}
.photo{border-radius:6px}
.hero .photo{height:140px;margin:22px -20px 0;border-radius:0;background:linear-gradient(135deg,#cfc6b8,#6e6a64 55%,#2d2c2a)}

.collage{height:130px;margin-top:18px;background:linear-gradient(120deg,#1d2433,#56627a 45%,#d9dce3)}
.product{background:var(--card);border:1px solid var(--line);border-radius:10px;padding:16px}
.product .photo{height:120px;background:radial-gradient(circle at 55% 50%,#d9825a,#8c4a2c 45%,#1b1b1b 70%,#fff 72%)}
.product h3{font-size:13px;font-weight:500;margin:12px 0 6px}
.link{color:var(--accent);font-size:10.5px;margin-top:8px;display:flex;gap:6px;align-items:center}
.factory{height:150px;margin-top:16px;background:linear-gradient(140deg,#1f4a5c,#5a7a80 50%,#9ab39c)}
.machine{height:110px;margin-bottom:16px;background:linear-gradient(135deg,#f1f2f4,#c6c9ce 60%,#2c2f34)}
.eyebrow{font-size:10.5px;color:var(--accent);margin-bottom:6px}
.h3{font-size:14px;font-weight:600;margin-bottom:8px}
.arrows{display:flex;gap:22px;justify-content:center;margin-top:12px;color:#6c4fd8;font-size:14px}

.footer{background:linear-gradient(180deg,#ffffff 60%,var(--blush))}
.footer .brand-name{font-size:22px;letter-spacing:1px}
.socials{display:flex;gap:10px;margin:12px 0 18px}
.socials span{width:22px;height:22px;border-radius:50%;background:var(--accent)}
.socials span:nth-child(2){background:#e8ecf4}
.f-h{font-size:11.5px;font-weight:600;margin:12px 0 6px}
.f-list{list-style:none;font-size:11px;color:#4b5063;display:flex;flex-direction:column;gap:5px}
.f-list li{display:flex;gap:7px;align-items:center}
.legal{font-size:9.5px;color:var(--muted);margin-top:16px;line-height:1.7}
</style>
</head>
<body>
<div class="page">
  <header class="intro">
    <div>
      <div class="brand"><span class="brand-mark"></span><span class="brand-name">BROVIMARK</span></div>
      <div class="brand-tag">LASER CUTTING AND WELDING EQUIPMENT</div>
    </div>
    <h1 class="intro-title">Landing Page<br>Mobile view</h1>
  </header>

  <main class="board">
    <section class="col">
      <article class="screen hero">
        <div class="top"><span class="mini">BROVIMARK</span>
          <svg width="16" height="12" viewBox="0 0 16 12"><path d="M1 2h14M1 6h14M1 10h14" stroke="#1a86e0" stroke-width="1.6"/></svg></div>
        <h1>Discover the Future of Manufacturing with Brovimark</h1>
        <p class="p">Forem ipsum dolor sit amet, consectetur adipiscing elit. Nunc vulputate libero et velit interdum, ac aliquet odio mattis. Class aptent taciti sociosqu ad litora torquent per conubia nostra, per inceptos himenaeos.</p>
        <span class="btn-solid">Get started now
          <svg width="12" height="10" viewBox="0 0 12 10"><path d="M1 5h10M7 1l4 4-4 4" stroke="#fff" fill="none" stroke-width="1.4"/></svg></span>
        <div class="photo" role="img" aria-label="Photo of a laser cutting production hall"></div>
      </article>
      <article class="screen">
        <h2 class="h2 blue">Discover About Brovimark</h2>
        <p class="p">SaaS become a common delivery model for many business application, including office software, messaging software, payroll processing software, DBMS software, management software</p>
      </article>
    </section>

    <section class="col">
      <article class="screen">
        <h2 class="h2">Reasons you should choose us.</h2>
        <p class="p">We share common trends and strategies for improving your rental income and making sure you stay in high demand.</p>
        <ul class="checks">
          <li><svg width="12" height="10" viewBox="0 0 12 10"><path d="M1 5l3 3 7-7" stroke="#6c4fd8" fill="none" stroke-width="1.6"/></svg>Fully Responsive</li>
          <li><svg width="12" height="10" viewBox="0 0 12 10"><path d="M1 5l3 3 7-7" stroke="#6c4fd8" fill="none" stroke-width="1.6"/></svg>Forem ipsum</li>
          <li><svg width="12" height="10" viewBox="0 0 12 10"><path d="M1 5l3 3 7-7" stroke="#6c4fd8" fill="none" stroke-width="1.6"/></svg>Sorem ipsum dolor sit</li>
          <li><svg width="12" height="10" viewBox="0 0 12 10"><path d="M1 5l3 3 7-7" stroke="#6c4fd8" fill="none" stroke-width="1.6"/></svg>Worem ipsum dolor</li>
        </ul>
        <span class="btn-outline">Book a service
          <svg width="11" height="11" viewBox="0 0 11 11"><path d="M6 1h4v4M10 1L5 6M8 7v3H1V3h3" stroke="#1a86e0" fill="none" stroke-width="1.2"/></svg></span>
        <div class="photo collage" role="img" aria-label="Collage of laser machines and branded display"></div>
      </article>
      <article class="screen">
        <h2 class="h2 blue">Discover About Brovimark</h2>
        <p class="p">SaaS become a common delivery model for many business application, including office software, messaging software, payroll processing software, DBMS software, management software</p>
        <div class="photo factory" role="img" aria-label="Photo of technicians at a laser cutting machine"></div>
        <div class="arrows"><span>‹</span><span>›</span></div>
      </article>
    </section>

    <section class="col">
      <article class="product">
        <div class="photo" role="img" aria-label="Photo of a copper welding wire spool"></div>
        <h3>Accesories</h3>
        <p class="p">Qorem ipsum dolor sit amet, consectetur adipiscing elit.</p>
        <span class="link">Learn more
          <svg width="11" height="9" viewBox="0 0 11 9"><path d="M1 4.5h9M6.5 1l3.5 3.5L6.5 8" stroke="#1a86e0" fill="none" stroke-width="1.2"/></svg></span>
      </article>
      <article class="screen">
        <div class="photo machine" role="img" aria-label="Photo of a laser source unit"></div>
        <p class="eyebrow">Services we offer for you</p>
        <h3 class="h3">Laser Equipment Repair</h3>
        <p class="p">In addition to providing domestically-stocked laser manufacturing equipment, Brovimark offers support and repair services on laser welding, laser cutting, and laser cleaning machinery.</p>
        <ul class="checks">
          <li><svg width="12" height="12" viewBox="0 0 12 12"><circle cx="6" cy="6" r="6" fill="#e3f7ea"/><path d="M3.5 6l1.8 1.8 3.4-3.6" stroke="#3cc46a" fill="none" stroke-width="1.3"/></svg>Torem ipsum dolor sit amet, consectetur adipiscing elit.</li>
          <li><svg width="12" height="12" viewBox="0 0 12 12"><circle cx="6" cy="6" r="6" fill="#e3f7ea"/><path d="M3.5 6l1.8 1.8 3.4-3.6" stroke="#3cc46a" fill="none" stroke-width="1.3"/></svg>Lorem ipsum dolor sit</li>
          <li><svg width="12" height="12" viewBox="0 0 12 12"><circle cx="6" cy="6" r="6" fill="#e3f7ea"/><path d="M3.5 6l1.8 1.8 3.4-3.6" stroke="#3cc46a" fill="none" stroke-width="1.3"/></svg>Worem ipsum dolor sit amet consectetur</li>
          <li><svg width="12" height="12" viewBox="0 0 12 12"><circle cx="6" cy="6" r="6" fill="#e3f7ea"/><path d="M3.5 6l1.8 1.8 3.4-3.6" stroke="#3cc46a" fill="none" stroke-width="1.3"/></svg>Jorem ipsum dolor sit amet consectetur consectetur</li>
          <li><svg width="12" height="12" viewBox="0 0 12 12"><circle cx="6" cy="6" r="6" fill="#e3f7ea"/><path d="M3.5 6l1.8 1.8 3.4-3.6" stroke="#3cc46a" fill="none" stroke-width="1.3"/></svg>Qorem ipsum dolor</li>
        </ul>
        <span class="btn-outline">Book a service
          <svg width="11" height="11" viewBox="0 0 11 11"><path d="M6 1h4v4M10 1L5 6M8 7v3H1V3h3" stroke="#1a86e0" fill="none" stroke-width="1.2"/></svg></span>
      </article>
    </section>

    <section class="col">
      <footer class="screen footer">
        <span class="btn-solid">Contact us
          <svg width="12" height="10" viewBox="0 0 12 10"><path d="M1 5h10M7 1l4 4-4 4" stroke="#fff" fill="none" stroke-width="1.4"/></svg></span>
        <div class="brand" style="margin-top:20px"><span class="brand-name">BROVIMARK</span></div>
        <div class="socials"><span></span><span></span><span></span></div>
        <p class="f-h">Pages</p>
        <ul class="f-list"><li>Home</li><li>Product</li><li>About</li><li>Services</li><li>Contact</li></ul>
        <p class="f-h">Contact</p>
        <ul class="f-list">
          <li><svg width="11" height="11" viewBox="0 0 11 11"><path d="M2 1l2 2-1 1.5a6 6 0 003.5 3.5L8 7l2 2-1.5 1.5C5 10 1 6 .5 2.5z" stroke="#4b5063" fill="none" stroke-width=".9"/></svg>555-014-2270</li>
          <li><svg width="11" height="9" viewBox="0 0 11 9"><rect x=".5" y=".5" width="10" height="8" stroke="#4b5063" fill="none"/><path d="M.5 .5l5 4 5-4" stroke="#4b5063" fill="none"/></svg>info@brovimark.com</li>
          <li><svg width="11" height="11" viewBox="0 0 11 11"><circle cx="5.5" cy="5.5" r="5" stroke="#4b5063" fill="none"/><path d="M5.5 2.5v3l2 1.5" stroke="#4b5063" fill="none"/></svg>Monday – Thursday 7:30 am – 4:30 pm</li>
          <li><svg width="11" height="12" viewBox="0 0 11 12"><path d="M5.5 11.5S1 7 1 4.5a4.5 4.5 0 019 0C10 7 5.5 11.5 5.5 11.5z" stroke="#4b5063" fill="none"/><circle cx="5.5" cy="4.5" r="1.5" fill="#4b5063"/></svg>Fernwood, IL 60123</li>
        </ul>
        <p class="legal">Copyright, Brovimark 2024. All rights reserved.<br>Terms &amp; Conditions</p>
      </footer>
    </section>
  </main>
</div>
</body>
</html>
```